Brightfield Homes needs a web design and brand identifier

Brightfield Homes is a pioneering approach by Victorian councils and four greenhouse alliances to support low income households to install solar systems with no upfront costs.

Brightfield Homes will commence in May 2017.

Brightfield Homes is looking for a designer to create a website banner incorporating a brand identifier for Brightfield Homes. The brand identifier will be used in Brightfield Homes promotional materials, such as flyers and mail outs.

The website banner and brand identifier should engender trust and confidence in the target group (retirees).

Reason: Hi, Thank you for your work so far. We've been given advice to get a separate logo designed (instead of trying to include this as part of the banner design). Sorry for not realising this until now - we're new to all this. So, I have a couple of preliminary logo designs that are being considered by our project control group. I will forward a copy of the logo once we have it. The project control group is looking for a web design that is unique to Brightfield Homes and a design that draws on the key elements of the program (i.e. it helps people save money and take control). The site should be friendly but not too informal as the target group is seniors. Here's a link to another community energy organisation: www.kindlewattnet.com.au/ Apologies again for the delays. Cheers, Doug

Target Market(s)

Home owning, low income, retirees

Industry/Entity Type

Non Profit

Number of Pages Required

1 page

Font styles to use
Sans Serif

Requirements
Must have
• Use of Brightfield Home name
• Must promote Brightfield Homes as safe, reliable and trustworthy
Nice to have
• Blue - to engender sense of safety and confidence (open to suggestions, though)
• Solar panels / the sun
Should not have
• Anything that is hard to read
• anything that promotes riskyness

```html
<!DOCTYPE html>
<html lang="en">
<head>
<meta charset="utf-8">
<title>Brightfield Homes</title>
<link href="https://fonts.googleapis.com/css2?family=Exo+2:wght@400;600;700;800&family=Open+Sans:wght@400;600;700&display=swap" rel="stylesheet">
<style>
:root{
  --blue:#2f8fd6;
  --blue-dark:#1f6fb3;
  --navy:#253447;
  --red:#e84c3d;
  --orange:#f39c2a;
  --yellow:#f7b92e;
  --grey:#e6e7e8;
  --light:#eef0f1;
  --text:#3d3d3d;
  --white:#ffffff;
}
*{margin:0;padding:0;box-sizing:border-box}
html,body{width:1200px;height:2769px;overflow:hidden;background:var(--white)}
body{font-family:"Open Sans",Arial,sans-serif;color:var(--text)}
.page{position:relative;width:1200px;height:2769px;overflow:hidden}
.abs{position:absolute}

/* hero */
.hero{left:0;top:0;width:1200px;height:602px;background:linear-gradient(100deg,#4a5a3a 0%,#6e7a4e 35%,#9a8868 60%,#7c6a4f 80%,#4d5a3a 100%)}
.topbar{left:0;top:0;width:1200px;height:92px;background:rgba(15,20,25,.72)}
.brand{left:0;top:0;width:520px;height:92px;background:var(--blue);clip-path:polygon(0 0,100% 0,90% 100%,0 100%);display:flex;align-items:center;padding-left:172px;color:var(--white);font-family:"Exo 2",sans-serif;font-weight:700;font-size:30px;white-space:nowrap}
.call{left:683px;top:10px;color:var(--white);display:flex;align-items:center;gap:10px}
.call small{display:block;font-size:10px;font-weight:600;letter-spacing:.5px}
.call strong{display:block;font-family:"Exo 2",sans-serif;font-size:24px;font-weight:600;line-height:1}
.quote-btn{left:888px;top:18px;height:28px;padding:0 14px;border-radius:14px;background:var(--red);color:var(--white);font-size:11.5px;font-weight:700;line-height:28px;letter-spacing:.3px}
.nav{left:576px;top:68px;display:flex;gap:30px;color:var(--white);font-size:11px;font-weight:700}
.hero-copy{left:172px;top:240px;width:420px;color:var(--white)}
.hero-copy .kicker{font-family:"Exo 2",sans-serif;font-size:24px;font-weight:400;letter-spacing:.3px}
.hero-copy h1{font-family:"Exo 2",sans-serif;font-size:64px;font-weight:800;line-height:1;margin-top:2px}
.hero-copy p{font-size:17px;line-height:27px;margin-top:24px}
.hero-phone{display:flex;align-items:center;gap:12px;margin-top:20px;font-size:26px}

/* welcome */
.section-title{width:1200px;text-align:center;font-family:"Exo 2",sans-serif;font-weight:700;color:#111}
.rule{width:50px;height:3px;background:var(--blue);left:575px}
.video{left:172px;top:746px;width:428px;height:240px;background:linear-gradient(180deg,#8fb8b2 0%,#78a59a 55%,#5f8f7e 100%)}
.play{left:352px;top:832px;width:66px;height:66px;border:4px solid var(--white);border-radius:50%}
.play::after{content:"";position:absolute;left:23px;top:16px;border-left:22px solid var(--white);border-top:13px solid transparent;border-bottom:13px solid transparent}
.watch{left:300px;top:906px;width:170px;text-align:center;color:var(--white);font-size:11px;font-weight:700}
.welcome-text{left:633px;top:748px;width:372px;font-size:14px;line-height:23px;color:#444}
.welcome-text p+p{margin-top:22px}

/* how it works */
.how{left:0;top:1047px;width:1200px;height:476px;background:var(--navy)}
.step{top:1176px;width:198px;height:286px;border-radius:4px;background:linear-gradient(160deg,var(--yellow),var(--orange));color:var(--white)}
.step .num{position:absolute;left:14px;top:-12px;width:32px;height:32px;border-radius:50%;background:var(--red);font-family:"Exo 2",sans-serif;font-size:15px;font-weight:700;text-align:center;line-height:32px}
.step .icon{position:absolute;left:42px;top:14px;width:114px;height:114px;border-radius:50%;border:5px solid var(--white);background:radial-gradient(circle,#fbd03a 0%,#f6a623 100%)}
.step p{position:absolute;left:14px;top:160px;width:170px;text-align:center;font-size:12px;line-height:19px}
.step .dot{position:absolute;left:96px;bottom:14px;width:6px;height:6px;border-radius:50%;background:rgba(255,255,255,.6)}

/* eligibility */
.eligible{left:0;top:1523px;width:611px;height:578px;background:var(--grey)}
.leaf{display:flex;align-items:center;justify-content:center;text-align:center;color:var(--white);font-size:12px;font-weight:700;line-height:16px;padding:0 18px;border:3px solid rgba(255,255,255,.55);box-shadow:0 0 0 2px rgba(0,0,0,.05)}
.leaf-tl{border-radius:30px 4px 30px 4px}
.leaf-tr{border-radius:4px 30px 4px 30px}
.elig-title{left:425px;top:1768px;font-family:"Exo 2",sans-serif;font-weight:700;font-size:25px;line-height:28px;color:#111}
.elig-sub{left:425px;top:1830px;font-size:12px;color:#555}
.who{left:611px;top:1523px;width:589px;height:578px;background:linear-gradient(180deg,#1a7fd8 0%,#4fa6e8 30%,#e06b3a 62%,#c4552c 80%,#eae4dc 100%)}
.who-copy{left:646px;top:1578px;width:530px;color:var(--white)}
.who-copy h2{font-family:"Exo 2",sans-serif;font-size:29px;font-weight:700;white-space:nowrap}
.who-copy p{width:370px;font-size:13.5px;line-height:22px;margin-top:12px}

/* what next */
.next{left:0;top:2101px;width:1200px;height:174px;background:var(--red);color:var(--white);text-align:center}
.next h2{font-family:"Exo 2",sans-serif;font-size:25px;font-weight:700;margin-top:30px}
.next .rule{position:absolute;top:76px;background:var(--white)}
.next p{font-size:12.5px;margin-top:32px}
.next .contact{font-family:"Exo 2",sans-serif;font-size:25px;font-weight:600;margin-top:8px}

/* partners */
.partners{left:0;top:2275px;width:1200px;height:230px;background:var(--light)}
.partner{top:2374px;height:80px;background:#c9ccce;border-radius:4px}

/* footer */
.footer{left:0;top:2505px;width:1200px;height:264px;background:var(--blue)}
.fcol{top:2530px;font-size:11px;line-height:22px;color:var(--white)}
.fcol h4{font-size:11.5px;font-weight:700;margin-bottom:12px;line-height:16px}
.fline{display:flex;gap:10px;margin-bottom:10px;line-height:16px}
.ficon{flex:none;width:22px;height:22px;border-radius:50%;border:2px solid var(--white)}
.socials{display:flex;gap:14px}
.socials span{width:20px;height:20px;border-radius:50%;border:2px solid var(--white)}
.input{width:196px;height:28px;background:var(--blue-dark);border:1px solid #5fb0ea;padding-left:10px;line-height:26px;font-size:11px;margin-bottom:10px;color:var(--white)}
.join{width:196px;height:30px;background:var(--red);text-align:center;line-height:30px;font-size:12px;font-weight:700;color:var(--white)}
.copy{left:172px;top:2740px;font-size:10px;color:var(--white)}
</style>
</head>
<body>
<div class="page">

  <div class="abs hero" role="img" aria-label="Photo of a smiling senior man in a hat leaning on a garden fence"></div>
  <div class="abs topbar"></div>
  <div class="abs brand">Brightfield Homes</div>
  <div class="abs call">
    <svg width="22" height="22" viewBox="0 0 24 24" fill="none" stroke="#fff" stroke-width="1.8"><path d="M5 3h4l2 5-2.5 1.5a11 11 0 0 0 6 6L16 13l5 2v4a2 2 0 0 1-2 2A16 16 0 0 1 3 5a2 2 0 0 1 2-2z"/></svg>
    <div><small>CALL NOW</small><strong>0400 555 218</strong></div>
  </div>
  <div class="abs quote-btn">REQUEST A QUOTE</div>
  <nav class="abs nav"><span>HOME</span><span>ABOUT US</span><span>SERVICES</span><span>HOW IT WORKS</span><span>CONTACT US</span></nav>
  <div class="abs hero-copy">
    <div class="kicker">HELP PENSIONER HOUSEHOLDS TO</div>
    <h1>SAVE MONEY</h1>
    <p>and take control of their energy bills by installing an affordable, quality solar system and be part of an Australian first</p>
    <div class="hero-phone">
      <svg width="26" height="26" viewBox="0 0 24 24" fill="none" stroke="#fff" stroke-width="1.6"><path d="M5 3h4l2 5-2.5 1.5a11 11 0 0 0 6 6L16 13l5 2v4a2 2 0 0 1-2 2A16 16 0 0 1 3 5a2 2 0 0 1 2-2z"/></svg>
      <span>0400 555 218</span>
    </div>
  </div>

  <h2 class="abs section-title" style="left:0;top:664px;font-size:30px">WELCOME TO BRIGHTFIELD HOMES</h2>
  <div class="abs rule" style="top:705px"></div>
  <div class="abs video" role="img" aria-label="Illustration of a green island with solar panels, wind turbines and a small house"></div>
  <div class="abs play"></div>
  <div class="abs watch">WATCH VIDEO</div>
  <div class="abs welcome-text">
    <p>We need you Help pensioner households to save money and take control of their energy bills by installing anaffordable, quality solar system and be part of an Australian first.</p>
    <p>Brightfield Homes is a pioneering approach by Victorian councils to support pensioner households to install solar with no upfront costs. We've done the hard work of finding a safe, reliable and quality installer so pensioners don't have to.</p>
  </div>

  <div class="abs how"></div>
  <h2 class="abs section-title" style="left:0;top:1096px;font-size:25px;color:#fff">HOW IT WORKS</h2>
  <div class="abs rule" style="top:1136px"></div>
  <div class="abs step" style="left:172px"><span class="num">01</span><div class="icon" role="img" aria-label="Sun with plug icon"></div><p>Brightfield Homes checks that every person gets a solar system that pays for itself in energy savings from day one</p><span class="dot"></span></div>
  <div class="abs step" style="left:391px"><span class="num">02</span><div class="icon" role="img" aria-label="Solar panel with battery icon"></div><p>Brightfield Homes organises for the solar system to be installed</p><span class="dot"></span></div>
  <div class="abs step" style="left:611px"><span class="num">03</span><div class="icon" role="img" aria-label="Senior person icon"></div><p>Brightfield Homes supports pensioners to understand and get the most out of solar</p><span class="dot"></span></div>
  <div class="abs step" style="left:831px"><span class="num">04</span><div class="icon" role="img" aria-label="Solar panel with zero percent icon"></div><p>Pensioners gradually pay for cost through their usual rates payments at 0% interest</p><span class="dot"></span></div>

  <div class="abs eligible"></div>
  <div class="abs leaf leaf-tl" style="left:172px;top:1611px;width:195px;height:194px;background:var(--navy)">HOMEOWNERS</div>
  <div class="abs leaf leaf-tr" style="left:384px;top:1567px;width:196px;height:178px;background:var(--blue)">PENSION CARD HOLDERS</div>
  <div class="abs leaf leaf-tr" style="left:186px;top:1824px;width:196px;height:179px;background:var(--blue-dark)">USUALLY AT HOME FROM 9AM TO 5PM</div>
  <div class="abs leaf leaf-tl" style="left:399px;top:1861px;width:195px;height:179px;background:var(--red)">AVERAGE TO HIGH ELECTRICITY USERS</div>
  <div class="abs elig-title">IS MY CLIENT<br>ELIGIBLE?</div>
  <div class="abs elig-sub">Refer clients who are:</div>
  <div class="abs who" role="img" aria-label="Photo of solar panels on a terracotta tiled roof under a blue sky"></div>
  <div class="abs who-copy">
    <h2>WHO IS BRIGHTFIELD HOMES?</h2>
    <p>Over 20 Victorian councils have come together with support from the Victorian Government's Clean Power Jobs Fund to run the Brightfield Home program.</p>
  </div>

  <section class="abs next">
    <h2>WHAT NEXT?</h2>
    <div class="rule"></div>
    <p>To refer clients or for further information, contact Doug Hensley at Brightfield Homes:</p>
    <div class="contact">Call us : 0400 555 218 &nbsp;|&nbsp; Email us : doug.hensley@ridgevale.vic.gov.au</div>
  </section>

  <div class="abs partners"></div>
  <h2 class="abs section-title" style="left:0;top:2316px;font-size:16px">BRIGHTFIELD HOMES IS A PARTNERSHIP BETWEEN</h2>
  <div class="abs rule" style="top:2346px"></div>
  <div class="abs partner" style="left:218px;width:150px"></div>
  <div class="abs partner" style="left:408px;width:196px"></div>
  <div class="abs partner" style="left:650px;width:172px"></div>
  <div class="abs partner" style="left:862px;width:110px"></div>

  <footer class="abs footer"></footer>
  <div class="abs fcol" style="left:172px"><h4>QUICK LINKS</h4>Home<br>About Us<br>Services<br>How It Works<br>Contact Us</div>
  <div class="abs fcol" style="left:296px"><h4>SUPPORT</h4>Contact us<br>FAQs<br>Legal<br>Privacy Policy<br>Legal</div>
  <div class="abs fcol" style="left:415px"><h4>CONTACT US</h4>
    <div class="fline"><span class="ficon"></span><span>Your Company LTD.<br>Street Name, 000000<br>City Name</span></div>
    <div class="fline"><span class="ficon"></span><span>Phone<br>0400 555 218</span></div>
    <div class="fline"><span class="ficon"></span><span>Email<br>doug.hensley@ridgevale.vic.gov.au</span></div>
  </div>
  <div class="abs fcol" style="left:648px"><h4>GET CONNECTED</h4><div class="socials"><span></span><span></span><span></span><span></span></div></div>
  <div class="abs fcol" style="left:831px"><h4>E-NEWSLETTER SIGNUP</h4><div class="input">Name</div><div class="input">Email</div><div class="join">JOIN</div></div>
  <div class="abs copy">© 2017 Brightfield Homes. All Rights Reserved</div>

</div>
</body>
</html>
```